A website where experts collaborate on your project

I am building a new website where experts (yes, like designers) collaborate on projects with the project owner. More minds = more collaboration = better end product. Please see Pelmora(dot)com for a quick landing page I created for collaborating on presentations (although there will be many project types offered)

I am looking for a DESIGNER LONG TERM, but for now, just need initial mock ups to show the web programmers.

I have 21 Word documents loosely designed, what I would like to see here is a theme. Please DO NOT GO OFF WHAT YOU CURRENTLY SEE AT PELMORA. What is up now is only a quick landing page.

You can view a Word doc of the homepage here:
https://www.filevanta.com/s/qx83kdm2/home.docx?dl=0

WHAT AM I LOOKING FOR?
A clean, well designed theme.

Here is a link to the logo:
https://www.filevanta.com/s/mr47tpz9/logo%20-%20horizontal.tif?dl=0
-----------------------------------------
Here are a few sites I like the design of and what I like about them:
www.quenbrook.com-all around my favorite, beautiful graphics, clean layout, bold use of colors on a dark background
Ravelto.com- clean layout, The use of humans and bubble style elements.
Mintharbor.com :) clean, bold, unique pop art style but professional
plumevault.com - From the unique colors and artwork and the ability of that art to not interfere with the important elements of the site
sparkwidgets.com-clean, nice colors, well organized and separated sections.
www.dunmereco.com-love the font, use of colors and sectionalized style

All in all, I am not picky and open to so many styles. I would ultimately like the designer I pick to design all 21 pages.
Updates

Hello everyone,Moving forward, I would like you all to pay special attention to the section in my brief titled "Here are a few sites I like the design of and what I like about them". Please see below, I handpicked each one of these as sites I really like. Thank you.Here are a few sites I like the design of and what I like about them:Ravelto.com- clean layout, The use of humans and bubble style elements.Mintharbor.com :) clean, bold, unique pop art style but professionalwriteraccess.com - From the unique colors and artwork and the ability of that art to not interfere with the important elements of the sitegrowthgeeks.com-clean, nice colors, well organized and separated sections.www.dunmereco.com-love the font, use of colors and sectionalized stylewww.quenbrook.com-beautiful graphics, clean layout, bold use of colors----------------------------------------- Added Tuesday, November 24, 2015

I updated the homepage, you can see it here:https://www.dropbox.com/s/kwlkbsookq3cg2m/1new%20homepage.docx?dl=0I am modeling it after my favorite designed site: triplelift.comI love the dark colors with the orange glowing style boldness of the buttons. It's real clean too. Added Tuesday, November 24, 2015

Target Market(s)

small business owners, marketers, freelancer writers, graphic designers,

Industry/Entity Type

Building

Number of Pages Required

5+ page

Requirements
Must have
• I can't think of anything the project must have.
Nice to have
• WHAT AM I LOOKING FOR?
• A clean, well designed theme. I had a designer do a bit of work putting elements together, I found it to be very plain, but I like the Application Page (https://www.filevanta.com/s/jb19ckr3/Pelmora-Website.ai?dl=0)
• Here is a link to the logo:
• https://www.filevanta.com/s/mr47tpz9/logo%20-%20horizontal.tif?dl=0
• Here are a few sites I like the design of and what I like about them:
• Ravelto.com- clean layout, The use of humans and bubble style elements.
• Mintharbor.com :) clean, bold, unique pop art style but professional
• plumevault.com - From the unique colors and artwork and the ability of that art to not interfere with the important elements of the site
• sparkwidgets.com-clean, nice colors, well organized and separated sections.
• www.dunmereco.com-love the font, use of colors and sectionalized style
• www.quenbrook.com-beautiful graphics, clean layout, bold use of colors
• -----------------------------------------
Should not have
• out of the boxed, templated style website. I want this site to be memorable and not look like a thousand others

```html
<!DOCTYPE html>
<html lang="en">
<head>
<meta charset="utf-8">
<title>Pelmora — Experts collaborating on your project</title>
<link href="https://fonts.googleapis.com/css2?family=Source+Sans+3:ital,wght@0,400;0,600;1,400&display=swap" rel="stylesheet">
<style>
:root{
  --orange:#f7941d;
  --teal:#5ab3cb;
  --teal-text:#4aa8c4;
  --ink:#2b2b2b;
  --gray-bg:#ededed;
  --footer:#161616;
  --white:#ffffff;
  --dot-dark:#2e3440;
}
*{margin:0;padding:0;box-sizing:border-box}
html,body{width:854px;height:1200px;overflow:hidden}
body{font-family:"Source Sans 3",sans-serif;color:var(--ink);background:var(--white);position:relative}
.abs{position:absolute}

/* header */
.site-header{position:absolute;left:0;top:0;width:854px;height:83px;background:var(--white)}
.brand{left:92px;top:26px;display:flex;align-items:center;gap:6px}
.brand-name{font-size:24px;font-weight:600;color:var(--orange);letter-spacing:-.3px}
.brand-dot{width:20px;height:20px;border-radius:50%;background:var(--orange)}
.search{left:286px;top:27px;width:142px;height:30px;border:1px solid #cfcfcf;display:flex;align-items:center;padding-left:8px;gap:6px;font-size:11px;color:#666}
.main-nav{left:451px;top:34px;display:flex;gap:15px;font-size:13px;color:var(--ink)}
.main-nav .active{color:var(--orange)}

/* hero */
.hero{position:absolute;left:0;top:83px;width:854px;height:299px;background:var(--orange);color:var(--white)}
.hero-title{left:90px;top:46px;font-size:33px;font-weight:400;line-height:1}
.hero-sub{left:90px;top:106px;font-size:22px;line-height:24px;font-weight:400}
.btn-outline{border:2px solid var(--white);color:var(--white);font-size:11.5px;font-weight:600;display:flex;align-items:center;justify-content:center}
.hero-cta{left:93px;top:207px;width:156px;height:36px}
.hero-art{left:464px;top:11px;width:276px;height:288px}

/* projects band */
.projects{position:absolute;left:0;top:382px;width:854px;height:487px;background:var(--gray-bg)}
.filters{left:27px;top:8px;width:322px;height:467px;background:var(--teal);color:var(--white)}
.filters-title{left:62px;top:64px;font-size:13px;font-weight:600;padding-bottom:4px;border-bottom:2px solid var(--white)}
.filter-rail{left:42px;top:99px;width:2px;height:163px;background:#2f6e80}
.filter-rail-mark{left:42px;top:124px;width:3px;height:18px;background:var(--white)}
.filter-list{left:62px;top:95px;list-style:none;font-size:12.5px;line-height:22px}
.slider{left:121px;top:110px;width:87px;height:3px;background:var(--white)}
.slider-knob{left:181px;top:103px;width:16px;height:16px;border-radius:50%;background:var(--white)}
.slider-max{left:238px;top:95px;font-size:12.5px;line-height:22px}
.save-filter{left:105px;top:386px;width:112px;height:33px;font-size:12.5px;font-weight:400}

.list-head{left:377px;top:63px;font-size:13px;font-weight:600;padding-bottom:4px;border-bottom:2px solid var(--ink);width:85px}
.sort{left:540px;top:58px;display:flex;align-items:center;gap:5px;font-size:12.5px}
.sort .on{color:var(--teal-text)}
.featured-box{left:370px;top:106px;width:412px;height:70px;border:2px solid var(--teal)}
.project{position:absolute;left:383px}
.project-title{font-size:14.5px;color:var(--teal-text);line-height:17px}
.project-meta{font-size:11.5px;line-height:16px}
.project-meta b{font-size:13px;font-weight:400}
.featured-tag{left:383px;top:233px;font-size:12.5px;color:var(--orange)}
.see-all{left:383px;top:407px;width:71px;height:27px;border:2px solid var(--ink);font-size:12.5px;display:flex;align-items:center;justify-content:center}

/* testimonial */
.testimonial{position:absolute;left:0;top:869px;width:854px;height:225px;background:var(--white)}
.quote{left:170px;top:70px;width:500px;text-align:center;font-style:italic;font-size:16.5px;line-height:16px}
.quote-mark{color:var(--teal);font-size:28px;font-weight:600;line-height:0}
.quote-by{right:191px;top:118px;font-size:15.5px}
.quote-by strong{font-weight:600}
.dots{left:407px;top:165px;display:flex;gap:3px}
.dots span{width:11px;height:11px;border-radius:50%;background:var(--dot-dark)}
.dots span.current{background:var(--teal)}

/* footer */
.site-footer{position:absolute;left:0;top:1094px;width:854px;height:106px;background:var(--footer);color:var(--white)}
.press{left:0;top:62px;width:854px;text-align:center;font-style:italic;font-size:12.5px}
</style>
</head>
<body>

<header class="site-header">
  <div class="abs brand"><span class="brand-name">pelmora</span><span class="brand-dot"></span></div>
  <div class="abs search">
    <svg width="16" height="10" viewBox="0 0 16 10"><circle cx="4.5" cy="4.5" r="3.3" fill="none" stroke="#f7941d" stroke-width="1.4"/><line x1="7" y1="7" x2="9.2" y2="9.2" stroke="#f7941d" stroke-width="1.4"/><path d="M11 4h4l-2 2.5z" fill="#f7941d"/></svg>
    <span>Search Project</span>
  </div>
  <nav class="abs main-nav">
    <span class="active">Home</span><span>Projects</span><span>How it Works</span><span>Plans</span><span>My Account</span>
  </nav>
</header>

<section class="hero">
  <h1 class="abs hero-title">Convert more customers</h1>
  <p class="abs hero-sub">Experience the power of<br>experts collaborating<br>on your project.</p>
  <a class="abs btn-outline hero-cta">GET STARTED</a>
  <div class="abs hero-art" role="img" aria-label="Illustration of two business professionals standing with arms crossed" style="background:linear-gradient(180deg,#f7941d 0%,#3a3a44 45%,#1f2230 100%);border-radius:120px 120px 0 0"></div>
</section>

<section class="projects">
  <aside class="abs filters">
    <h2 class="abs filters-title">Filters</h2>
    <div class="abs filter-rail"></div>
    <div class="abs filter-rail-mark"></div>
    <ul class="abs filter-list">
      <li>Price $20</li><li>Country</li><li>Categories</li><li>Time Left</li>
      <li>Active L Expired</li><li>Contains adult content</li><li>Keywords</li><li>Followers</li><li>+ more</li>
    </ul>
    <div class="abs slider"></div>
    <div class="abs slider-knob"></div>
    <span class="abs slider-max">$1,000+</span>
    <a class="abs btn-outline save-filter">SAVE FILTER</a>
  </aside>

  <h2 class="abs list-head">Crowd Projects</h2>
  <div class="abs sort">
    <span>Sort:</span>
    <svg width="22" height="22" viewBox="0 0 22 22"><path d="M3 12l9-9h7v7l-9 9z" fill="none" stroke="#4aa8c4" stroke-width="1.3"/><circle cx="15.5" cy="6.5" r="1.4" fill="none" stroke="#4aa8c4"/></svg>
    <span class="on">Price</span><span>|</span>
    <svg width="16" height="22" viewBox="0 0 16 22"><path d="M8 21C3 14 1.5 11 1.5 8a6.5 6.5 0 0113 0c0 3-1.5 6-6.5 13z" fill="none" stroke="#2b2b2b" stroke-width="1.3"/><circle cx="8" cy="8" r="2.3" fill="none" stroke="#2b2b2b" stroke-width="1.2"/></svg>
    <span>country</span><span>|</span>
    <svg width="21" height="21" viewBox="0 0 21 21"><circle cx="10.5" cy="10.5" r="9" fill="none" stroke="#2b2b2b" stroke-width="1.4"/><path d="M10.5 5v6h4" fill="none" stroke="#2b2b2b" stroke-width="1.4"/></svg>
    <span>Time left</span>
  </div>

  <div class="abs featured-box"></div>
  <div class="project" style="top:119px"><div class="project-title">Morbi in ante arcu. Maecenas sit amet sem vel</div><div class="project-meta"><b>$80</b>, U.K. , time left: <b>6 days</b></div></div>
  <div class="project" style="top:196px"><div class="project-title">Lorem ipsum dolor sit amet, consectetur adipiscing</div><div class="project-meta"><b>$90</b>, CA., time left: <b>6 days</b></div></div>
  <span class="abs featured-tag">Featured</span>
  <div class="project" style="top:250px"><div class="project-title">Neque porro quisquam est qui dolorem ipsum</div><div class="project-meta"><b>$250</b>, U.S., time left: <b>6 days</b></div></div>
  <div class="project" style="top:301px"><div class="project-title">Duis ligula sapien, sodales id tortor vitae, ornare</div><div class="project-meta"><b>$62</b>, U.K., time left: <b>6 days</b></div></div>
  <div class="project" style="top:352px"><div class="project-title">Neque porro quisquam est qui dolorem ipsum</div><div class="project-meta"><b>$48</b>, U.S., time left: <b>6 days</b></div></div>
  <a class="abs see-all">SEE ALL</a>
</section>

<section class="testimonial">
  <p class="abs quote"><span class="quote-mark">&ldquo;</span>With Pelmora I have multiple experts perfecting my content<br>and I only pay for the feedback I find valuable. It’s perfect <span class="quote-mark">&rdquo;</span></p>
  <p class="abs quote-by"><strong>Dana Whitlow</strong>, CEO, Northgate 52</p>
  <div class="abs dots"><span class="current"></span><span></span><span></span></div>
</section>

<footer class="site-footer">
  <p class="abs press">Media Logos | Media Logos | Media Logos | Media Logos</p>
</footer>

</body>
</html>
```